New Business card design to reflect rebrand

I would like a business card design with a good base colour for our new logo and also a placeholder for a profile pic of the card holder. the design needs to be editable to the point that we can easily change the picture of the person and use that design for printmerlo etc. we are looking at a metalic finish business card so will need a good base colour to bring out the finish.

Target Market(s)

prospective customers

Industry/Entity Type

Business

Contact Information for Business Card

I would like one editable design that we can change the name of the card holder and profile picture. The design need to be in a format that be send to printmerlo etc.

Our address is Fenwick Lodge, Copse Lane, Elmbury Cross, GU14 3TP Tel no. 01483 556172

Requirements
Must have
• place holder for a profile pic for the card holder. in AI or preferably PSD format

```html
<!DOCTYPE html>
<html lang="en">
<head>
<meta charset="utf-8">
<title>Corvane Workplace Services – Business Card</title>
<link href="https://fonts.googleapis.com/css2?family=Open+Sans:wght@400;600;700&display=swap" rel="stylesheet">
<style>
  :root {
    --navy: #3d5270;
    --navy-dark: #2f4360;
    --navy-light: #4d6584;
    --orange: #e8691c;
    --paper: #ffffff;
    --paper-shade: #eceef1;
    --ink: #4a4f57;
    --photo: #a9abae;
    --photo-light: #c9cacc;
    --stage: #e4e2de;
  }
  * { box-sizing: border-box; margin: 0; padding: 0; }
  html, body { width: 1200px; height: 843px; overflow: hidden; }
  body {
    background: var(--stage);
    font-family: "Open Sans", Arial, sans-serif;
    display: flex;
    align-items: center;
    justify-content: center;
    gap: 40px;
  }
  .card {
    position: relative;
    width: 540px;
    height: 309px;
    border-radius: 4px;
    overflow: hidden;
    box-shadow: 0 10px 26px rgba(0,0,0,0.18);
  }

  /* Back side */
  .card--back {
    background: linear-gradient(160deg, var(--navy-light), var(--navy) 55%, var(--navy-dark));
    display: flex;
    flex-direction: column;
    align-items: center;
    justify-content: center;
    gap: 22px;
  }
  .brand {
    display: flex;
    align-items: center;
    gap: 12px;
  }
  .brand__mark {
    width: 16px;
    height: 16px;
    background: var(--orange);
  }
  .brand__name {
    font-weight: 700;
    letter-spacing: 0.06em;
    text-transform: uppercase;
    line-height: 1.15;
  }
  .brand__name span { display: block; }
  .card--back .brand__name { color: #ffffff; font-size: 26px; }
  .web {
    color: #dfe5ee;
    font-size: 14px;
    letter-spacing: 0.35em;
  }

  /* Front side */
  .card--front {
    background: linear-gradient(135deg, var(--paper) 40%, var(--paper-shade));
  }
  .card--front .brand { position: absolute; left: 50px; top: 40px; }
  .card--front .brand__name { color: var(--navy); font-size: 21px; }
  .address {
    position: absolute;
    left: 50px;
    top: 132px;
    color: var(--ink);
    font-size: 14px;
    line-height: 1.3;
    font-style: normal;
  }
  .phone {
    position: absolute;
    left: 50px;
    top: 200px;
    display: flex;
    align-items: center;
    gap: 8px;
    color: var(--ink);
    font-size: 14px;
  }
  .phone svg { width: 12px; height: 12px; fill: var(--orange); }
  .profile {
    position: absolute;
    right: 58px;
    top: 92px;
    width: 118px;
    text-align: center;
  }
  .profile__photo {
    width: 118px;
    height: 110px;
    border-radius: 6px;
    background: linear-gradient(180deg, var(--photo-light), var(--photo));
  }
  .profile__name {
    margin-top: 8px;
    color: var(--navy);
    font-weight: 700;
    font-size: 16px;
  }
  .profile__role {
    color: var(--orange);
    font-weight: 600;
    font-size: 13px;
  }
  .card__rule {
    position: absolute;
    left: 0;
    right: 0;
    bottom: 33px;
    height: 2px;
    background: var(--orange);
  }
  .card__band {
    position: absolute;
    left: 0;
    right: 0;
    bottom: 0;
    height: 28px;
    background: var(--navy);
  }
</style>
</head>
<body>
  <section class="card card--back" aria-label="Card back">
    <div class="brand">
      <span class="brand__mark"></span>
      <p class="brand__name"><span>Corvane</span><span>Workplace Services</span></p>
    </div>
    <p class="web">www.corvane.co.uk</p>
  </section>

  <section class="card card--front" aria-label="Card front">
    <div class="brand">
      <span class="brand__mark"></span>
      <p class="brand__name"><span>Corvane</span><span>Workplace Services</span></p>
    </div>
    <address class="address">
      Fenwick Lodge<br>
      Copse Lane, Elmbury Cross<br>
      GU14 3TP
    </address>
    <p class="phone">
      <svg viewBox="0 0 24 24" aria-hidden="true"><path d="M6.6 10.8a15.1 15.1 0 0 0 6.6 6.6l2.2-2.2a1 1 0 0 1 1-.25 11.4 11.4 0 0 0 3.6.57 1 1 0 0 1 1 1V20a1 1 0 0 1-1 1A17 17 0 0 1 3 4a1 1 0 0 1 1-1h3.5a1 1 0 0 1 1 1c0 1.25.2 2.45.57 3.57a1 1 0 0 1-.25 1z"/></svg>
      01483 556172
    </p>
    <div class="profile">
      <div class="profile__photo" role="img" aria-label="Profile photo of the card holder"></div>
      <p class="profile__name">Daniel Reeve</p>
      <p class="profile__role">CEO/Founder</p>
    </div>
    <div class="card__rule"></div>
    <div class="card__band"></div>
  </section>
</body>
</html>
```